Web design for small empirical brand consulting company that will sell a web-based brand tool

We need a totally new and very appealing website:
Purpose: We want to attract lots of potential customers with this website... especially, we want to sell our web-based tool valuquant®... we want to be perceived as innovative, trendy, but solid and reliable… we want customers go to the website, login at „valuquant®“ (see structure), and perceive how it works.. and the contacting us or in the near future being able to buy a login and work with the tool… so we want to a) inform (on the website or send the url to customers) and b) to „force“ potential customers getting in contact with us…
Structure (e.g.): Must Home, valuquant®, About us, Contact (incl. legal notice); we are open for more, Nice to have e.g. references/clients, press... for example, we publish a nice book in a couple of months and might want to show it somewhere on the website as well...)
Layout: We would like to have more/mainly figures - may be animated or something like that – in specific those on slides 7 and 8 as well as 6 and 9 (which would be for our web-based tool valuquant®...)... excellent, but simple and with few text…
Fonts: Eurostile; CMYK 100/23/100/19, CMYK 0/0/0/70
Logo: Would you please use the lorentavo-logo used in this file?
Social Media: we think that it might make sense to be connected to chatterbay, quipline and so on as well…
Phantasy: May be it is possible to have something between a classic marketing research and an e-commerce website... just a thought... because it is mainly about the new tool that will be assessable through a login... but customers might want to contact us or vice versa in order to check how the tool will work (btw: you do not have further info about valuquant® here... I know)… I dream of having a site where people go to and by components of our tool like at brimbo… click and buy and go for it…
It is possible to program it in php or java? Thanks.
Pages I personally like: Don’t know if that helps, but I personally like those websites just they seem so simple: http:// www.pellivarn.com/, http://www.craftelune.net/... but I am veeery open
Pages I do not like anymore: my own www.lorentavo.ch

```html
<!DOCTYPE html>
<html lang="en">
<head>
<meta charset="utf-8">
<title>lorentavo – valuquant®</title>
<link href="https://fonts.googleapis.com/css2?family=Questrial&family=Roboto:wght@300;400;700;900&display=swap" rel="stylesheet">
<style>
:root{
  --green:#137b3f;
  --green-dark:#0f6a35;
  --grey:#4d4d4d;
  --grey-btn:#6b6b6b;
  --text:#333333;
  --muted:#666666;
  --footer:#141414;
  --footer-link:#6f6f6f;
  --white:#ffffff;
}
*{box-sizing:border-box;margin:0;padding:0}
html,body{width:738px;height:1200px;overflow:hidden;background:var(--white)}
body{font-family:"Questrial",sans-serif;color:var(--text);position:relative}

.site-header{height:47px;display:flex;align-items:center;padding:0 24px 0 33px;position:relative}
.brand{font-family:"Questrial",sans-serif;font-size:21px;color:var(--grey);display:flex;align-items:center;gap:5px;letter-spacing:-.3px}
.brand-mark{width:9px;height:16px;background:var(--green)}
.main-nav{position:absolute;left:226px;top:0;height:47px;display:flex;gap:17px;align-items:center}
.main-nav a{font-family:"Roboto",sans-serif;font-size:9px;color:#555;text-decoration:none;letter-spacing:.2px;height:47px;line-height:48px}
.main-nav a.active{color:var(--green);border-bottom:2px solid var(--green);line-height:46px}
.account{margin-left:auto;display:flex;gap:7px}
.account a{font-family:"Roboto",sans-serif;font-size:9px;color:var(--white);text-decoration:none;height:26px;line-height:26px;padding:0 12px}
.btn-login{background:var(--green)}
.btn-register{background:var(--grey-btn)}

.hero{height:343px;position:relative;overflow:hidden}
.hero-photo{position:absolute;inset:0;background:radial-gradient(ellipse at 55% 25%,#8a7f78 0%,#5a524d 30%,#2a2a2c 65%,#151517 100%)}
.hero-content{position:relative;text-align:center;color:var(--white);padding-top:133px}
.hero-kicker{font-family:"Roboto",sans-serif;font-weight:300;font-size:19px;letter-spacing:.3px}
.hero-title{font-family:"Roboto",sans-serif;font-weight:900;font-size:29px;margin-top:4px;letter-spacing:.3px}
.hero-cta{display:inline-block;margin-top:17px;border:1px solid #ddd;width:99px;height:31px;line-height:30px;font-family:"Roboto",sans-serif;font-size:9px;color:var(--white);text-decoration:none;background:rgba(0,0,0,.25)}
.hero-dots{display:flex;justify-content:center;gap:5px;margin-top:42px}
.hero-dots span{width:9px;height:9px;border-radius:50%;background:#bdbdbd}
.hero-dots span.on{background:var(--green)}

.intro{text-align:center;font-size:13px;line-height:18px;color:#333;padding-top:41px}

.features{display:grid;grid-template-columns:repeat(4,1fr);padding:0 25px;margin-top:48px;text-align:center}
.feature-icon{height:56px;display:flex;justify-content:center;align-items:center}
.feature h3{font-weight:400;font-size:14px;color:#222;margin-top:14px}
.feature p{font-size:10px;line-height:12.5px;color:var(--muted);margin-top:7px;padding:0 8px}

.team{position:absolute;top:697px;left:0;width:738px;height:265px;background:var(--green);color:var(--white)}
.team h2{font-weight:400;font-size:24px;text-align:center;padding-top:19px}
.team-rule{width:200px;height:1px;margin:10px auto 0;background:linear-gradient(90deg,transparent,rgba(255,255,255,.35),transparent)}
.team-grid{display:grid;grid-template-columns:325px 325px;column-gap:0;row-gap:25px;margin:34px 0 0 85px}
.member{display:flex;gap:17px}
.member-photo{width:49px;height:66px;background:linear-gradient(#cdbfb2,#8d7b6c)}
.member h4{font-weight:400;font-size:13.5px;margin-top:2px}
.member p{font-size:10px;line-height:12.5px;color:#cfe3d5;margin-top:7px;width:210px}

.offers{position:absolute;top:991px;left:32px;display:flex;gap:18px}
.offer{width:212px;height:59px;background:var(--grey);color:var(--white);display:flex;align-items:center;justify-content:space-between;padding:0 15px;font-family:"Roboto",sans-serif;font-size:15px;text-decoration:none}
.offer.current{background:var(--green)}

.site-footer{position:absolute;top:1082px;left:0;width:738px;height:118px;background:var(--footer)}
.footer-nav{display:flex;justify-content:center;gap:17px;padding-top:27px}
.footer-nav a{font-family:"Roboto",sans-serif;font-size:8.5px;color:var(--footer-link);text-decoration:none}
.footer-nav a.active{color:var(--green)}
.social{display:flex;justify-content:center;gap:14px;margin-top:28px}
.social a{display:flex;align-items:center;gap:4px;font-size:9px;color:#9a9a9a;text-decoration:none}
.social span{width:14px;height:14px;border-radius:50%;background:#9a9a9a}
</style>
</head>
<body>
<header class="site-header">
  <div class="brand"><span class="brand-mark"></span>lorentavo</div>
  <nav class="main-nav">
    <a class="active" href="#">HOME</a><a href="#">VALUQUANT</a><a href="#">ABOUT US</a><a href="#">CONTACT</a><a href="#">CLIENTS</a>
  </nav>
  <div class="account"><a class="btn-login" href="#">LOGIN</a><a class="btn-register" href="#">REGISTER</a></div>
</header>

<section class="hero">
  <div class="hero-photo" role="img" aria-label="Businessman in a dark suit pointing towards the viewer"></div>
  <div class="hero-content">
    <p class="hero-kicker">SIMPLY MEASURING AND MODELING</p>
    <h1 class="hero-title">YOUR BRAND SUCCESS</h1>
    <a class="hero-cta" href="#">KNOW MORE</a>
    <div class="hero-dots"><span class="on"></span><span></span><span></span><span></span><span></span></div>
  </div>
</section>

<p class="intro">valuquant® provides a means to be closer to your customers,<br>more security, more precise communication – all of which means more success</p>

<section class="features">
  <div class="feature">
    <div class="feature-icon"><svg width="58" height="42" viewBox="0 0 58 42" fill="#137b3f"><path d="M0 6h10v22H0zM48 6h10v22H48z"/><path d="M10 9l10-4 8 3 8-3 12 4v17l-6 5-4-3-3 4-4-3-3 4-4-3-3 4-5-4-6-4z"/><path d="M20 14l8-5 6 3" stroke="#fff" stroke-width="2" fill="none"/></svg></div>
    <h3>Closeness</h3>
    <p>valuquant® letsyou get even closer to your target groups. ! valuquant® supports customer relations.</p>
  </div>
  <div class="feature">
    <div class="feature-icon"><svg width="48" height="52" viewBox="0 0 48 52" fill="#137b3f"><rect x="0" y="40" width="9" height="12"/><rect x="13" y="33" width="9" height="19"/><rect x="26" y="26" width="9" height="26"/><rect x="39" y="18" width="9" height="34"/><path d="M8 28l24-20-4-4h14v14l-4-4L14 34z"/></svg></div>
    <h3>Security</h3>
    <p>valuquant® letsyou get even closer to your target groups. ! valuquant® supports customer relations.</p>
  </div>
  <div class="feature">
    <div class="feature-icon"><svg width="50" height="50" viewBox="0 0 50 50" fill="#137b3f"><path d="M0 0h16l-5 5 9 9-6 6-9-9-5 5zM50 0v16l-5-5-9 9-6-6 9-9-5-5zM0 50V34l5 5 9-9 6 6-9 9 5 5zM50 50H34l5-5-9-9 6-6 9 9 5-5z"/></svg></div>
    <h3>Fit</h3>
    <p>valuquant® letsyou get even closer to your target groups. ! valuquant® supports customer relations.</p>
  </div>
  <div class="feature">
    <div class="feature-icon"><svg width="48" height="44" viewBox="0 0 48 44" fill="#137b3f"><path d="M0 24l5-4 13 13L44 0l4 3-29 41z"/></svg></div>
    <h3>Customer Loyalty</h3>
    <p>valuquant® letsyou get even closer to your target groups. ! valuquant® supports customer relations.</p>
  </div>
</section>

<section class="team">
  <h2>Our Team</h2>
  <div class="team-rule"></div>
  <div class="team-grid">
    <div class="member"><div class="member-photo" role="img" aria-label="Portrait of Jonas Albrecht"></div><div><h4>Jonas Albrecht, Dr</h4><p>Excepteur sint occaecat cupidatat non proident, sunt in culpa qui officia deserunt mollit anim id est laborum.</p></div></div>
    <div class="member"><div class="member-photo" role="img" aria-label="Portrait of Lorenz Wieland"></div><div><h4>Lorenz Wieland, M.A.</h4><p>Excepteur sint occaecat cupidatat non proident, sunt in culpa qui officia deserunt mollit anim id est laborum.</p></div></div>
    <div class="member"><div class="member-photo" role="img" aria-label="Portrait of Matthias Kerber"></div><div><h4>Matthias Kerber, Dr. des.</h4><p>Excepteur sint occaecat cupidatat non proident, sunt in culpa qui officia deserunt mollit anim id est laborum.</p></div></div>
    <div class="member"><div class="member-photo" role="img" aria-label="Handwritten note held up in place of a portrait" style="background:linear-gradient(#e8ebe9,#c9cfcc)"></div><div><h4>Niklas Ostner, M.A.*</h4><p>Excepteur sint occaecat cupidatat non proident, sunt in culpa qui officia deserunt mollit anim id est laborum.</p></div></div>
  </div>
</section>

<nav class="offers">
  <a class="offer" href="#">COMPANY BRAND<svg width="19" height="19" viewBox="0 0 19 19"><circle cx="9.5" cy="9.5" r="8.5" fill="none" stroke="#fff" stroke-width="1.5"/><path d="M5 8.5h5V5.5l4 4-4 4v-3H5z" fill="#fff"/></svg></a>
  <a class="offer current" href="#">PRODUCT SERVICE<svg width="19" height="19" viewBox="0 0 19 19"><circle cx="9.5" cy="9.5" r="8.5" fill="none" stroke="#fff" stroke-width="1.5"/><path d="M5 8.5h5V5.5l4 4-4 4v-3H5z" fill="#fff"/></svg></a>
  <a class="offer" href="#">CEO BRAND<svg width="19" height="19" viewBox="0 0 19 19"><circle cx="9.5" cy="9.5" r="8.5" fill="none" stroke="#fff" stroke-width="1.5"/><path d="M5 8.5h5V5.5l4 4-4 4v-3H5z" fill="#fff"/></svg></a>
</nav>

<footer class="site-footer">
  <nav class="footer-nav">
    <a class="active" href="#">HOME</a><a href="#">VALUQUANT</a><a href="#">ABOUT US</a><a href="#">CONTACT</a><a href="#">CLIENTS</a><a href="#">LEGAL NOTICE</a>
  </nav>
  <div class="social">
    <a href="#"><span></span>chatterbay</a>
    <a href="#"><span></span>quipline</a>
    <a href="#"><span></span>gatherly</a>
    <a href="#"><span></span>linkwell</a>
  </div>
</footer>
</body>
</html>
```